Webdesign für Kleingruppenreisen in die Südsteiermark
Zielgruppe
Wir sind ein Start-Up Unternehmen, das als Kleingruppenreisen in die Südsteiermark veranstaltet; der Schwerpunkt liegt auf dem Kulinarischen. Zielgruppe sind Geschäftsleute, die diese Kurzreisen (Do-So) für Marketingzwecke oder als Mitarbeiterbonus (oder auch privat) nutzen möchten.
Aufgabenstellung
Die Homepage soll eine Online-Shop Möglichkeit bieten, in der die Reise (bisher gibt es nur einen Ablauf) gebucht werden kann. Optisch sollte sie sich an das bereits von Ihnen erstellte Logo anlehnen und möglichst ansprechende Fotos von der Südsteiermark, Graz, Leoben usw. enthalten. (Siehe die beiden Flyer und das Logo)
Wir haben inzwischen Bildfreigaben von Haldauer und dem Tourismusverband Kellwinden erhalten und können auch eigene Bilder zur Verfügung stellen. Bitte kontaktieren Sie uns dafür, wenn nötig.

```html
<!DOCTYPE html>
<html lang="en">
<head>
<meta charset="utf-8">
<title>Gaumenweg Reisen – Small Group Trips to Southern Styria</title>
<link href="https://fonts.googleapis.com/css2?family=Lato:wght@300;400;700;900&family=Great+Vibes&display=swap" rel="stylesheet">
<style>
:root{
  --yellow:#f6dd2f;
  --yellow-text:#f5d43c;
  --green:#4bb631;
  --green-dark:#3e9c27;
  --green-head:#6cc33c;
  --orange:#f05a22;
  --orange-light:#f08a3a;
  --purple:#a22fd6;
  --amber:#f6b21c;
  --pink:#e6386a;
  --ink:#222;
  --text:#444;
  --muted:#777;
  --line:#e3e3e3;
  --black:#050505;
  --white:#fff;
}
*{box-sizing:border-box;margin:0;padding:0}
html,body{width:1200px;height:3307px;overflow:hidden}
body{position:relative;font-family:'Lato',sans-serif;color:var(--text);background:var(--white)}
.abs{position:absolute}

/* header */
.site-header{position:absolute;left:0;top:0;width:1200px;height:90px;background:var(--white);z-index:3}
.brand{position:absolute;left:87px;top:26px;width:185px;height:96px;background:var(--white);display:flex;align-items:center;justify-content:center;gap:8px;z-index:4}
.brand-mark{width:14px;height:14px;border-radius:50%;background:var(--orange)}
.brand-name{font-weight:900;font-size:19px;color:var(--orange);letter-spacing:.2px}
.main-nav{position:absolute;top:27px;left:554px;display:flex;height:41px;align-items:center}
.main-nav a{font-size:16px;color:var(--ink);text-decoration:none;text-transform:uppercase;position:absolute;white-space:nowrap}
.main-nav a.active{background:var(--yellow);height:41px;width:85px;display:flex;align-items:center;justify-content:center;left:0;border-radius:2px}

/* hero */
.hero{position:absolute;left:0;top:90px;width:1200px;height:427px;
  background:linear-gradient(180deg,#3c4b5e 0%,#5e6156 35%,#6a5a3c 65%,#3b3a24 100%)}
.hero-title{position:absolute;left:0;width:1200px;top:100px;text-align:center;font-family:'Great Vibes',cursive;font-size:92px;line-height:98px;color:var(--white)}
.hero-dots{position:absolute;top:388px;left:576px;display:flex;gap:6px}
.hero-dots span{width:15px;height:15px;border-radius:50%;background:var(--white)}
.hero-dots span:first-child{background:var(--yellow)}

/* section headings */
.section-title{position:absolute;left:0;width:1200px;text-align:center;font-weight:900;font-size:37px;color:var(--ink);letter-spacing:-.5px}
.section-title em{font-style:normal;color:var(--yellow-text)}
.intro{position:absolute;left:170px;width:860px;top:600px;text-align:center;font-size:21px;line-height:35px;font-weight:300;color:#333}

/* trip cards */
.trip-card{position:absolute;top:703px;width:262px;height:362px;border:1px solid var(--line);background:var(--white)}
.trip-card h3{height:50px;line-height:50px;text-align:center;font-weight:900;font-size:22px;color:var(--ink);text-transform:uppercase}
.trip-card h3 em{font-style:normal;color:var(--yellow-text)}
.trip-photo{height:177px}
.trip-card p{font-size:12.5px;line-height:20px;text-align:center;padding:10px 12px 0;color:#555}
.trip-foot{position:absolute;left:0;right:0;bottom:0;height:56px;border-top:1px solid var(--line);padding:10px 17px}
.trip-foot small{display:block;font-size:8px;color:#333;text-transform:uppercase}
.trip-foot strong{font-size:16px;font-weight:700;color:#222}
.btn-green{position:absolute;background:var(--green);color:var(--white);font-size:13px;text-align:center;border-radius:2px}
.trip-foot .btn-green{right:22px;top:12px;width:100px;height:27px;line-height:27px}

/* video band */
.video-band{position:absolute;left:0;top:1117px;width:1200px;height:432px}

/* features */
.feature{position:absolute;top:1608px;width:215px}
.feature-icon{position:absolute;left:0;top:0;width:50px;height:50px;background:var(--green);border-radius:2px}
.feature-icon svg{display:block}
.feature h4{position:absolute;left:66px;top:6px;font-weight:400;font-size:15px;line-height:19px;color:#444}
.feature p{position:absolute;left:0;top:74px;width:207px;font-size:12.5px;line-height:27px;color:#444;text-align:justify}

.rule{position:absolute;left:548px;top:1921px;width:104px;height:4px;background:#222}

/* packages */
.package{position:absolute;top:1970px;width:262px;height:362px;border:1px solid var(--line);background:var(--white)}
.package-head{height:55px;color:var(--white);font-weight:900;font-size:12.5px;line-height:20px;text-align:center;padding-top:8px;text-transform:uppercase}
.package-photo{height:138px}
.package h5{font-weight:400;font-size:15px;line-height:18px;text-align:center;padding:10px 20px 0}
.package p{font-size:12px;line-height:19px;text-align:center;padding:8px 14px 0;color:#555}
.package-meta{position:absolute;left:0;right:0;top:289px;border-top:1px solid var(--line);text-align:center;font-size:8.5px;color:#888;padding-top:11px}
.package .btn-green{left:76px;top:318px;width:100px;height:24px;line-height:24px}

/* orange info */
.info-band{position:absolute;left:0;top:2372px;width:1200px;height:545px;background:var(--orange)}
.tabs{position:absolute;left:87px;top:55px;width:493px;height:67px;background:#ececec;display:flex}
.tab{height:67px;line-height:64px;font-size:19px;color:#222;text-align:center}
.tab.active{background:var(--white);border-bottom:5px solid var(--green);width:175px}
.info-text{position:absolute;left:87px;top:166px;width:492px;font-size:17px;line-height:31.2px;color:#fde3a0;text-align:justify;font-weight:400}
.devices{position:absolute;left:610px;top:40px;width:590px;height:465px}

/* footer */
.footer-stripe{position:absolute;left:0;top:2917px;width:1200px;height:6px;background:var(--yellow)}
.site-footer{position:absolute;left:0;top:2923px;width:1200px;height:337px;background:var(--black)}
.site-footer h6{position:absolute;top:20px;font-weight:700;font-size:20px;color:var(--green-head);text-transform:uppercase}
.footer-menu a{position:absolute;font-size:13px;color:var(--white);text-decoration:none;text-transform:uppercase;white-space:nowrap}
.footer-menu a.strong{font-size:15px}
.contact-row{position:absolute;left:441px;display:flex;gap:14px;align-items:flex-start}
.contact-row svg{flex:none;width:22px}
.contact-row span{font-size:12.5px;line-height:27px;color:var(--white)}
.footer-brand{position:absolute;left:252px;top:221px;width:145px;height:77px;background:var(--white);display:flex;align-items:center;justify-content:center;gap:6px}
.footer-brand .brand-mark{width:10px;height:10px}
.footer-brand .brand-name{font-size:14px}
.field{position:absolute;left:834px;width:277px;background:var(--white);border:1px solid #ccc;font-size:15px;color:#666;padding:8px 18px}
.submit{position:absolute;left:834px;top:256px;width:140px;height:41px;background:var(--yellow);font-size:19px;text-align:center;line-height:41px;color:#222}
.copyright{position:absolute;left:0;top:3260px;width:1200px;height:47px;background:#1b1b1b;text-align:center;line-height:47px;font-size:12px;color:var(--white)}
</style>
</head>
<body>

<header class="site-header">
  <div class="brand"><span class="brand-mark"></span><span class="brand-name">Gaumenweg Reisen</span></div>
  <nav class="main-nav">
    <a class="active" href="#">Home</a>
    <a href="#" style="left:98px">Services</a>
    <a href="#" style="left:199px">Online Shop</a>
    <a href="#" style="left:332px">Blog</a>
    <a href="#" style="left:403px">Legal</a>
    <a href="#" style="left:483px">Contact</a>
  </nav>
</header>

<section class="hero" role="img" aria-label="Aerial photo of Graz old town at dusk with church towers and hills">
  <h1 class="hero-title">Experience The<br>Excitement!</h1>
  <div class="hero-dots"><span></span><span></span><span></span><span></span></div>
</section>

<h2 class="section-title" style="top:538px">Why Choosing &nbsp;<em>US?</em></h2>
<p class="intro">Lorem Ipsum is simply dummy text of the printing and typesetting industry. Lorem Ipsum has been the industry's standard dummy text ever since the 1500s</p>

<article class="trip-card" style="left:133px">
  <h3>Business <em>Trips</em></h3>
  <div class="trip-photo" role="img" aria-label="Hotel garden with blue pool and parasols" style="background:linear-gradient(160deg,#4d7a3c 0%,#7ea85a 45%,#2fa6de 70%,#c9d4c8 100%)"></div>
  <p>Lorem Ipsum is simply dummy text of the printing and typesetting industry. Lorem Ipsum has been the industry's</p>
  <div class="trip-foot"><small>Starts from</small><strong>$ 499</strong><span class="btn-green">View details</span></div>
</article>
<article class="trip-card" style="left:468px">
  <h3>Private <em>Trips</em></h3>
  <div class="trip-photo" role="img" aria-label="Graz clock tower above red rooftops in evening light" style="background:linear-gradient(180deg,#7fa8d4 0%,#b6c6d4 40%,#8a5a3a 75%,#5b3a28 100%)"></div>
  <p>Lorem Ipsum is simply dummy text of the printing and typesetting industry. Lorem Ipsum has been the industry's</p>
  <div class="trip-foot"><small>Starts from</small><strong>$ 299</strong><span class="btn-green">View details</span></div>
</article>
<article class="trip-card" style="left:800px">
  <h3>Short <em>Trips</em></h3>
  <div class="trip-photo" role="img" aria-label="Aerial view of a river town surrounded by green hills" style="background:linear-gradient(170deg,#8aa0a8 0%,#9a8c7c 40%,#5f7f4a 70%,#3e6a6a 100%)"></div>
  <p>Lorem Ipsum is simply dummy text of the printing and typesetting industry. Lorem Ipsum has been the industry's</p>
  <div class="trip-foot"><small>Starts from</small><strong>$ 199</strong><span class="btn-green">View details</span></div>
</article>

<svg class="video-band" viewBox="0 0 1200 432" width="1200" height="432" role="img" aria-label="Vineyard hills of Southern Styria at sunset with a farmhouse, tinted orange, with a play button">
  <defs>
    <linearGradient id="bandGrad" x1="0" y1="0" x2="0" y2="1">
      <stop offset="0" stop-color="#f28a3c"/>
      <stop offset=".45" stop-color="#e0712c"/>
      <stop offset="1" stop-color="#9c4a1c"/>
    </linearGradient>
  </defs>
  <polygon points="0,0 600,22 1200,0 1200,432 600,408 0,432" fill="url(#bandGrad)"/>
  <circle cx="603" cy="215" r="91" fill="none" stroke="#fff" stroke-width="5"/>
  <circle cx="603" cy="215" r="71" fill="#fff"/>
  <polygon points="583,182 583,248 638,215" fill="#c9561c"/>
</svg>

<div class="feature" style="left:87px">
  <div class="feature-icon"></div>
  <h4>Special<br>Activities</h4>
  <p>Lorem Ipsum is simply dummy text of the printing and typesetting industry. Lorem Ipsum has been the industry's standard dummy text ever since the 1500s</p>
</div>
<div class="feature" style="left:354px">
  <div class="feature-icon"></div>
  <h4>Travel<br>Arrangements</h4>
  <p>Lorem Ipsum is simply dummy text of the printing and typesetting industry. Lorem Ipsum has been the industry's standard dummy text ever since the 1500s</p>
</div>
<div class="feature" style="left:630px">
  <div class="feature-icon"></div>
  <h4>Private<br>Guide</h4>
  <p>Lorem Ipsum is simply dummy text of the printing and typesetting industry. Lorem Ipsum has been the industry's standard dummy text ever since the 1500s</p>
</div>
<div class="feature" style="left:903px">
  <div class="feature-icon"></div>
  <h4>Location<br>Manager</h4>
  <p>Lorem Ipsum is simply dummy text of the printing and typesetting industry. Lorem Ipsum has been the industry's standard dummy text ever since the 1500s</p>
</div>

<h2 class="section-title" style="top:1866px;font-size:33px">BEST HOLIDAY <em>PACKAGES</em></h2>
<div class="rule"></div>

<article class="package" style="left:130px">
  <div class="package-head" style="background:var(--purple)">Summer stay for single couple<br>@ $250.00 for 4 nights</div>
  <div class="package-photo" role="img" aria-label="Wine glasses on a terrace table overlooking vineyard hills" style="background:linear-gradient(180deg,#7fa0c8 0%,#6f9a3e 40%,#4d7a2a 75%,#c9a470 100%)"></div>
  <h5 style="color:var(--purple)">The Green Heart of Austria - Vacations Styria</h5>
  <p>Lorem Ipsum is simply dummy text of the printing and typesetting industry.</p>
  <div class="package-meta">No of Days: 5 &nbsp;|&nbsp; People: 4</div>
  <span class="btn-green">Book Now</span>
</article>
<article class="package" style="left:468px">
  <div class="package-head" style="background:var(--amber)">Winter stay for single couple @<br>$250.00 for 2 nights</div>
  <div class="package-photo" role="img" aria-label="River island pavilion in Graz with green trees" style="background:linear-gradient(180deg,#9ab0c0 0%,#4f7040 40%,#5a7d86 70%,#b0bcc4 100%)"></div>
  <h5 style="color:var(--amber)">Christmas Markets In-Exploring Graz</h5>
  <p>Lorem Ipsum is simply dummy text of the printing and typesetting industry.</p>
  <div class="package-meta">No of Days: 5 &nbsp;|&nbsp; People: 4</div>
  <span class="btn-green">Book Now</span>
</article>
<article class="package" style="left:802px">
  <div class="package-head" style="background:var(--pink)">Summer stay for single couple<br>@ $250.00 for 3 nights</div>
  <div class="package-photo" role="img" aria-label="Ornate red historic building facade at night" style="background:linear-gradient(180deg,#2a2530 0%,#9a3a32 40%,#b8504a 70%,#3a2a24 100%)"></div>
  <h5 style="color:var(--pink)">See it! Feel it! Love it! - Leoben</h5>
  <p>Lorem Ipsum is simply dummy text of the printing and typesetting industry.</p>
  <div class="package-meta">No of Days: 5 &nbsp;|&nbsp; People: 4</div>
  <span class="btn-green">Book Now</span>
</article>

<section class="info-band">
  <div class="tabs">
    <div class="tab active">Why Best ?</div>
    <div class="tab" style="width:115px">Features</div>
    <div class="tab" style="width:203px">Store the Goods</div>
  </div>
  <p class="info-text">Lorem Ipsum is simply dummy text of the printing and typesetting industry. Lorem Ipsum has been the industry's standard dummy text ever since the 1500s. Lorem Ipsum is simply dummy text of the printing and typesetting industry. Lorem Ipsum has been the industry's standard dummy text ever since the 1500s. Lorem Ipsum is simply dummy text of the printing and typesetting industry. Lorem Ipsum has been the industry's standard dummy text ever since the 1500s. Lorem Ipsum is simply dummy text of the printing and typesetting industry. Lorem Ipsum has been the industry's standard dummy text ever since the 1500s.</p>
  <div class="devices" role="img" aria-label="Illustration of the website shown on desktop, laptop, tablet and phone screens" style="background:radial-gradient(ellipse at 55% 50%,#f4f1ec 0%,#d9d4cc 35%,rgba(240,90,34,0) 70%)"></div>
</section>

<div class="footer-stripe"></div>
<footer class="site-footer">
  <h6 style="left:112px">Menu</h6>
  <nav class="footer-menu">
    <a href="#" style="left:113px;top:77px">Home</a>
    <a href="#" style="left:113px;top:113px">Services</a>
    <a href="#" class="strong" style="left:113px;top:146px">Online Shop</a>
    <a href="#" style="left:113px;top:183px">Blog</a>
    <a href="#" style="left:113px;top:219px">Legal</a>
    <a href="#" style="left:113px;top:254px">Contact</a>
    <a href="#" style="left:252px;top:77px">Terms &amp; Condition</a>
    <a href="#" style="left:252px;top:113px">Privacy Policy</a>
    <a href="#" style="left:252px;top:148px">Sitemap</a>
  </nav>
  <div class="footer-brand"><span class="brand-mark"></span><span class="brand-name">Gaumenweg Reisen</span></div>

  <h6 style="left:477px">Contact &nbsp;Us</h6>
  <div class="contact-row" style="top:72px">
    <svg viewBox="0 0 20 28" height="28"><path d="M10 0C4.5 0 0 4.4 0 9.8 0 17 10 28 10 28s10-11 10-18.2C20 4.4 15.5 0 10 0zm0 14a4.3 4.3 0 1 1 0-8.6 4.3 4.3 0 0 1 0 8.6z" fill="#fff"/></svg>
    <span>Lorem Ipsum is simply dummy text of the<br>printing and typesetting industry</span>
  </div>
  <div class="contact-row" style="top:138px">
    <svg viewBox="0 0 22 16" height="16"><rect x="1" y="1" width="20" height="14" fill="none" stroke="#fff" stroke-width="1.5"/><path d="M1 1l10 8 10-8" fill="none" stroke="#fff" stroke-width="1.5"/></svg>
    <span style="line-height:16px">info@gaumenweg-post.de</span>
  </div>
  <div class="contact-row" style="top:184px">
    <svg viewBox="0 0 24 24" height="24"><path d="M6.6 10.8a15.1 15.1 0 0 0 6.6 6.6l2.2-2.2c.3-.3.7-.4 1-.2 1.1.4 2.3.6 3.6.6.6 0 1 .4 1 1V20c0 .6-.4 1-1 1A17 17 0 0 1 3 4c0-.6.4-1 1-1h3.5c.6 0 1 .4 1 1 0 1.3.2 2.5.6 3.6.1.3 0 .7-.2 1z" fill="#fff"/></svg>
    <span style="line-height:24px">000-555-0142</span>
  </div>

  <h6 style="left:829px">Get &amp; Touch with us</h6>
  <div class="field" style="top:65px;height:35px">Name</div>
  <div class="field" style="top:112px;height:34px">Email id</div>
  <div class="field" style="top:158px;height:84px">Comments</div>
  <div class="submit">SUBMIT</div>
</footer>
<div class="copyright">copyright@ www.gaumenwegreisen.de</div>

</body>
</html>
```